Nutrition business needs logo & business card design

We need a business card & logo design for a new company based in Toronto, Ontario Canada called Verdel Wellworks.

We provide nutrition service using metrics as guide to manage client's progress. Our service creates individualized nutrition and lifestyle strategies that focuses on improving Performance, Longevity and Weight Loss. I would like to see designs that use the color of green, gray, blue and white.

The final design should:

--convey a feeling of connectedness with positive transformation.

-- communicate the idea of awareness with guided effort that yields personal independence for a better and more productive life

Target Market(s)

Professionals who work in the IT/Computer/Engineering/Banking industry specifically Directors, Managers, CEO's.

Industry/Entity Type

Health And Wellness

Contact Information for Business Card

Dorvane Pike, Owner
email: DPIKE@verdelwellworks.example
tel: - 555-204-7718

Logo Text

better health through analytics or measure to manage

Font styles to use
Other font styles liked:
• Garamound

Colors
ffffff
abd037
85acd3
757575
34a7d7

Requirements
Must have
• Good contrast and decent size font - ease of readability, aesthetically nice colors
Nice to have
• image of chart or graph that conveys measurement or analytics
Should not have
• Borders, images of food,

```html
<!DOCTYPE html>
<html lang="en">
<head>
<meta charset="utf-8">
<title>Verdel Wellworks – Business Card</title>
<link href="https://fonts.googleapis.com/css2?family=Open+Sans:wght@400;600&display=swap" rel="stylesheet">
<style>
  :root {
    --bg: #5a514c;
    --card: #050505;
    --card-glow: #1c1c1c;
    --green: #3cb014;
    --blue: #1488ef;
    --white: #ffffff;
    --faint: rgba(255,255,255,0.04);
  }
  * { margin: 0; padding: 0; box-sizing: border-box; }
  html, body { width: 1200px; height: 844px; overflow: hidden; }
  body {
    background: var(--bg);
    font-family: "Open Sans", Arial, sans-serif;
    position: relative;
  }
  .card {
    position: absolute;
    top: 272px;
    width: 520px;
    height: 300px;
    overflow: hidden;
    box-shadow: 0 10px 24px rgba(0,0,0,0.45);
  }
  /* Back side: contact details */
  .card--back {
    left: 50px;
    background: radial-gradient(ellipse at 65% 45%, var(--card-glow), var(--card) 70%);
  }
  .band { position: absolute; left: 0; width: 100%; height: 14px; }
  .band--top { top: 0; background: var(--green); }
  .band--bottom { bottom: 0; background: var(--blue); }
  .decor-circle {
    position: absolute;
    left: -70px; top: 60px;
    width: 260px; height: 260px;
    border-radius: 50%;
    background: var(--faint);
  }
  .identity {
    position: absolute;
    left: 210px; top: 62px;
    text-align: right;
  }
  .identity__name {
    font-size: 16px;
    font-weight: 600;
    letter-spacing: 0.5px;
    color: var(--blue);
    padding-bottom: 2px;
    border-bottom: 1px solid var(--blue);
  }
  .identity__name .surname { color: var(--green); }
  .identity__role {
    font-size: 12px;
    color: var(--white);
    margin-top: 2px;
    text-align: center;
  }
  .contact {
    position: absolute;
    left: 0; right: 0; top: 148px;
    text-align: center;
    color: var(--white);
    font-size: 12.5px;
    line-height: 17px;
    padding-left: 100px;
  }
  .contact__address {
    font-size: 14px;
    margin-top: 18px;
  }

  /* Front side: brand */
  .card--front {
    left: 630px;
    background: radial-gradient(ellipse at 55% 35%, var(--card-glow), var(--card) 65%);
  }
  .accent { position: absolute; }
  .accent--green { right: 0; top: 36px; width: 28px; height: 34px; background: var(--green); }
  .accent--blue { left: 0; bottom: 70px; width: 34px; height: 34px; background: var(--blue); }
  .brand {
    position: absolute;
    left: 0; right: 0; top: 70px;
    text-align: center;
  }
  .brand__dot {
    display: block;
    width: 74px; height: 74px;
    margin: 0 auto 18px;
    border-radius: 50%;
    border: 3px solid var(--blue);
  }
  .brand__name {
    font-size: 30px;
    font-weight: 400;
    color: var(--blue);
    letter-spacing: -0.3px;
  }
</style>
</head>
<body>
  <section class="card card--back" aria-label="Business card, contact side">
    <div class="band band--top"></div>
    <div class="decor-circle"></div>
    <div class="identity">
      <p class="identity__name">DORVANE <span class="surname">PIKE</span></p>
      <p class="identity__role">Managing Director</p>
    </div>
    <div class="contact">
      <p>555-204-7718</p>
      <p>555-204-7719</p>
      <p>dpike@verdelwellworks.example</p>
      <p>www.verdelwellworks.example</p>
      <p class="contact__address">88 Orchard Lane | Toronto, ON | M5V 2T6</p>
    </div>
    <div class="band band--bottom"></div>
  </section>

  <section class="card card--front" aria-label="Business card, brand side">
    <div class="accent accent--green"></div>
    <div class="brand">
      <span class="brand__dot"></span>
      <p class="brand__name">Verdel Wellworks</p>
    </div>
    <div class="accent accent--blue"></div>
  </section>
</body>
</html>
```